Business Card

Just need business logo with phone number on it. 0487 312 654
And the following on the bottom of the card.

"Your local plumbing experts".
and emblems for zelpa card, cheque and cash

```html
<!DOCTYPE html>
<html lang="en">
<head>
<meta charset="utf-8">
<title>Ridgeline Plumbing &amp; Drainage — Business Card</title>
<link rel="stylesheet" href="https://fonts.googleapis.com/css2?family=Open+Sans:wght@400;600;700;800&display=swap">
<style>
  :root {
    --canvas-bg: #ece9e4;
    --card-bg: #ffffff;
    --brand-red: #e8222a;
    --brand-blue: #1c8fd6;
    --text-grey: #4f4f50;
    --card-shadow: 0 6px 14px rgba(0, 0, 0, 0.28);
  }
  * { margin: 0; padding: 0; box-sizing: border-box; }
  html, body {
    width: 1200px;
    height: 1000px;
    overflow: hidden;
  }
  body {
    background: var(--canvas-bg);
    font-family: "Open Sans", Arial, sans-serif;
    position: relative;
  }
  .card {
    position: absolute;
    left: 266px;
    width: 666px;
    height: 396px;
    background: var(--card-bg);
    box-shadow: var(--card-shadow);
    display: flex;
    flex-direction: column;
    align-items: center;
  }
  .card--front { top: 74px; justify-content: center; }
  .card--back { top: 534px; padding-top: 72px; }

  .brand {
    display: flex;
    align-items: center;
    gap: 14px;
  }
  .brand__dot {
    width: 26px;
    height: 26px;
    border-radius: 50%;
    background: var(--brand-blue);
    flex: none;
  }
  .brand__name {
    color: var(--brand-red);
    font-weight: 800;
    text-transform: uppercase;
    line-height: 1.05;
    letter-spacing: 0.04em;
  }
  .card--front .brand__name { font-size: 34px; }
  .card--back .brand__name { font-size: 30px; }
  .brand__name span { display: block; }

  .contact {
    margin-top: 34px;
    text-align: center;
    color: var(--text-grey);
    font-size: 16px;
    line-height: 22px;
  }
  .contact__name {
    color: var(--brand-red);
    font-weight: 700;
    font-size: 20px;
    letter-spacing: 0.02em;
    margin-bottom: 8px;
  }
  .contact__tagline {
    font-weight: 700;
    margin-top: 10px;
  }
</style>
</head>
<body>
  <section class="card card--front" aria-label="Card front">
    <div class="brand">
      <div class="brand__dot" aria-hidden="true"></div>
      <p class="brand__name"><span>Ridgeline</span><span>Plumbing &amp; Drainage</span></p>
    </div>
  </section>

  <section class="card card--back" aria-label="Card back">
    <div class="brand">
      <div class="brand__dot" aria-hidden="true"></div>
      <p class="brand__name"><span>Ridgeline</span><span>Plumbing &amp; Drainage</span></p>
    </div>
    <div class="contact">
      <p class="contact__name">DALE MORRISSEY</p>
      <p class="contact__phone">0487 312 654</p>
      <p class="contact__email">info@ridgelineplumbing.com.au</p>
      <p class="contact__tagline">“Your local plumbing experts"</p>
      <p class="contact__payments">Emblems for zelpa card, cheque and cash</p>
    </div>
  </section>
</body>
</html>
```